Business Card, A4 Letter Head and DL Envelope for Brandvelle

We are looking for a design for our Business Card, A4 Letter Head and DL Envelope.

Brandvelle is a distributor of promotional products. We specialize in a range of branded promotional products, these include pens, polo shirts, key rings, drink bottles, uniforms and bags to name a few. We are experts in marketing and assist companies in choosing the right promotional product for their needs. We will predominately be an online business where customers visit our website and browse our range of promotional products and branding options.

Our colours are black, red, white and grey.

Files must be supplied in eps, pdf and ai format.

Please display the following information:
Derek Halloway
Account Manager
Suite xxx, 212 Ferrow Lane Melbourne, Victoria 3000
Phone +61 3 5550 1827
Mobile +61 455 016 342
sales@brandvelle-example.com.au
www.brandvelle-example.com.au

```html
<!DOCTYPE html>
<html lang="en">
<head>
<meta charset="utf-8">
<title>Brandvelle Business Card</title>
<link rel="stylesheet" href="https://fonts.googleapis.com/css2?family=Arimo:wght@400;700&family=Exo+2:wght@700&display=swap">
<style>
  :root {
    --brand-red: #be1e24;
    --card-white: #ffffff;
    --ink: #1a1a1a;
    --wordmark-grey: #4a4a4a;
    --name-grey: #e6e6e6;
    --mark-grey: #c9c9c9;
    --stage-top: #6a6a6a;
    --stage-bottom: #7c7c7c;
  }
  * { margin: 0; padding: 0; box-sizing: border-box; }
  html, body { width: 1200px; height: 1000px; overflow: hidden; }
  body {
    background: linear-gradient(180deg, var(--stage-top), var(--stage-bottom));
    font-family: "Arimo", Arial, sans-serif;
    position: relative;
  }
  .card {
    position: absolute;
    top: 342px;
    width: 528px;
    height: 316px;
    background: var(--card-white);
    box-shadow: 0 4px 8px rgba(0,0,0,0.35);
    overflow: hidden;
  }
  .card-front { left: 52px; }
  .card-back { left: 628px; }

  /* front */
  .front-panel {
    position: absolute;
    left: 250px; top: 0;
    width: 278px; height: 316px;
    background: var(--brand-red);
  }
  .holder-name {
    position: absolute;
    left: 272px; top: 18px;
    font-family: "Exo 2", Arial, sans-serif;
    font-weight: 700;
    font-size: 25px;
    color: var(--name-grey);
    letter-spacing: 0.3px;
    white-space: nowrap;
  }
  .holder-role {
    position: absolute;
    left: 272px; top: 49px;
    font-size: 15px;
    color: var(--name-grey);
  }
  .front-mark {
    position: absolute;
    left: 80px; top: 80px;
    width: 64px; height: 64px;
    border-radius: 50%;
    background: var(--mark-grey);
  }
  .front-wordmark {
    position: absolute;
    left: 28px; top: 153px;
    font-weight: 700;
    font-size: 19px;
    color: var(--wordmark-grey);
    text-transform: uppercase;
    letter-spacing: 0.5px;
  }
  .contact-list {
    position: absolute;
    left: 27px; top: 183px;
    list-style: none;
    font-size: 13.5px;
    color: var(--ink);
    line-height: 19px;
  }
  .contact-label {
    display: inline-block;
    width: 19px;
    color: var(--brand-red);
  }
  .contact-email { font-size: 12.8px; }
  .address {
    position: absolute;
    left: 26px; top: 247px;
    font-size: 13.5px;
    line-height: 19px;
    color: var(--brand-red);
    font-style: normal;
  }

  /* back */
  .back-mark {
    position: absolute;
    left: 204px; top: 42px;
    width: 120px; height: 120px;
    border-radius: 50%;
    background: var(--mark-grey);
  }
  .back-wordmark {
    position: absolute;
    left: 0; top: 190px;
    width: 528px;
    text-align: center;
    font-weight: 700;
    font-size: 38px;
    color: var(--wordmark-grey);
    text-transform: uppercase;
    letter-spacing: 0.5px;
  }
  .back-band {
    position: absolute;
    left: 0; top: 258px;
    width: 528px; height: 58px;
    background: var(--brand-red);
    display: flex;
    align-items: center;
    justify-content: center;
    color: var(--card-white);
    font-size: 15px;
  }
</style>
</head>
<body>
  <section class="card card-front" aria-label="Business card front">
    <div class="front-panel"></div>
    <div class="holder-name">Derek Halloway</div>
    <div class="holder-role">Account Manager</div>
    <div class="front-mark"></div>
    <div class="front-wordmark">Brandvelle</div>
    <ul class="contact-list">
      <li><span class="contact-label">M</span>+61 455 016 342</li>
      <li><span class="contact-label">T</span>+61 3 5550 1827</li>
      <li class="contact-email"><span class="contact-label">E</span>sales@brandvelle-example.com.au</li>
    </ul>
    <address class="address">Suite xxx, 212 Ferrow Lane<br>Melbourne, Victoria 3000</address>
  </section>

  <section class="card card-back" aria-label="Business card back">
    <div class="back-mark"></div>
    <div class="back-wordmark">Brandvelle</div>
    <div class="back-band">www.brandvelle-example.com.au</div>
  </section>
</body>
</html>
```